Pet sitting Business needs a website

We need a website that shows our services and prices. Shows our love of animals but also our professionalism. want a gallery, about, blog, services, links to fb and instagram accounts, newsletter archive. want it to be easy to access and wonderful to navigate. want the domain to be Birchfordpawhaven.com
take any info from FB site www.facebook.com/birchfordpawhaven
I would like it to fit square space platform

Target Market(s)

upscale area, responsible pet owners,

Industry/Entity Type

Pet Care

Coding

Coded - Design and coding required

Number of Pages Required

5+ page

Font styles to use
Sans Serif

Requirements
Must have
• (square space platform)
• Menu
• photo gallery
• about us
• services
• policies
• monthly newsletter
• unavailable dates
• Introduction (welcome)
• payment methods
• Daily updates
• testimonials (use from fb site)
Should not have
• stock photos

```html
<!DOCTYPE html>
<html lang="en">
<head>
<meta charset="utf-8">
<title>Birchford Paw Haven — Pet Sitting</title>
<link rel="stylesheet" href="https://fonts.googleapis.com/css2?family=Raleway:wght@600;700;800&family=Open+Sans:ital,wght@0,400;0,600;0,700;1,400&display=swap">
<style>
:root{
  --blue:#1a7eae;
  --blue-dark:#11648e;
  --navy:#13283d;
  --gold:#d9a52f;
  --gold-deep:#c98f15;
  --gold-text:#e0a526;
  --ice:#eef5f9;
  --ink:#3f4a52;
  --muted:#7a8288;
  --footer:#2b2b2b;
  --white:#ffffff;
}
*{box-sizing:border-box;margin:0;padding:0}
html,body{width:1200px;height:2821px;overflow:hidden}
body{font-family:"Open Sans",Arial,sans-serif;color:var(--ink);background:var(--white);position:relative}
h1,h2,h3,h4{font-family:"Raleway",Arial,sans-serif}
.wrap{width:1000px;margin:0 auto;position:relative}

/* header */
.topline{height:4px;background:var(--blue)}
.masthead{height:116px}
.masthead .wrap{height:116px;display:flex;align-items:center;justify-content:space-between}
.brand{display:flex;align-items:center;gap:10px}
.brand-dot{width:26px;height:26px;border-radius:50%;background:var(--gold)}
.brand-name{font-family:"Raleway",Arial,sans-serif;font-weight:700;font-size:22px;color:var(--gold-deep)}
.head-right{display:flex;align-items:center;gap:24px}
.phone{display:flex;align-items:center;gap:12px;font-size:17px;color:var(--navy)}
.lang{border:1px solid #ccc;border-radius:3px;padding:6px 12px;font-size:12px;color:#555;display:flex;align-items:center;gap:8px}
.lang i{display:block;width:20px;height:13px;background:#25407a}

/* nav */
.mainnav{height:50px;background:linear-gradient(#2a8fc0,var(--blue-dark));border-bottom:2px solid #0c5478}
.mainnav ul{list-style:none;display:flex;justify-content:space-between;height:48px;align-items:center}
.mainnav a{color:var(--white);text-decoration:none;font-family:"Raleway",Arial,sans-serif;font-weight:700;font-size:13px;letter-spacing:.3px}

/* hero */
.hero{height:513px;position:relative;background:linear-gradient(120deg,#3b3530 0%,#5a4a40 45%,#7a5a48 70%,#2c2622 100%);overflow:hidden}
.hero-shade{position:absolute;inset:0;background:linear-gradient(90deg,rgba(0,0,0,.55),rgba(0,0,0,0) 60%)}
.hero .wrap{padding-top:118px}
.hero h1{color:var(--white);font-size:34px;font-weight:800;margin:20px 0 14px}
.hero p{color:#eee;font-size:12.5px;line-height:24px;width:560px}
.btn-gold{display:inline-block;background:linear-gradient(var(--gold),var(--gold-deep));color:var(--white);font-family:"Raleway",Arial,sans-serif;font-weight:700;font-size:13px;padding:14px 28px;border-radius:3px;margin-top:20px}
.arrow{position:absolute;top:50%;transform:translateY(-50%)}

/* welcome */
.welcome{height:384px}
.welcome .wrap{display:flex;gap:44px;padding-top:52px}
.video{width:364px;height:278px;border:4px solid #e8e8e8;background:linear-gradient(135deg,#6a5646,#a48670 60%,#4a3a30);position:relative;flex:none}
.play{position:absolute;left:50%;top:50%;transform:translate(-50%,-50%)}
.welcome h2{font-size:28px;font-weight:800;color:var(--navy);margin-bottom:14px}
.welcome h2 span{color:var(--gold-text)}
.welcome p{font-size:12px;line-height:28px;text-align:justify}

/* services */
.services{height:458px;background:linear-gradient(rgba(214,162,44,.92),rgba(214,162,44,.92)),linear-gradient(90deg,#9b8a4a,#c8a450);text-align:center;color:var(--white)}
.services .wrap{padding-top:44px}
.section-title{font-size:28px;font-weight:800}
.intro{font-size:12px;line-height:28px;width:720px;margin:12px auto 0}
.service-row{display:flex;justify-content:space-between;margin-top:38px;padding:0 20px}
.service{width:300px}
.ring{width:128px;height:128px;border-radius:50%;border:3px solid var(--white);margin:0 auto;display:flex;align-items:center;justify-content:center}
.ring span{width:112px;height:112px;border-radius:50%;background:var(--white);display:flex;align-items:center;justify-content:center}
.service h3{font-size:14px;font-weight:700;margin:20px 0 8px}
.service p{font-size:12px;line-height:24px}

/* gallery */
.gallery{height:580px;background:var(--ice);text-align:center}
.gallery .wrap{padding-top:34px}
.gallery .section-title{color:var(--navy)}
.gallery .intro{color:var(--ink)}
.thumbs{display:grid;grid-template-columns:repeat(4,228px);gap:30px 29px;margin-top:30px}
.thumb{height:164px;border:3px solid var(--white)}

/* policies & testimonials */
.info{height:421px}
.info .wrap{display:flex;justify-content:space-between;padding-top:40px}
.info h2{font-size:24px;font-weight:800;color:var(--navy);margin-bottom:18px}
.info h2 span{color:var(--gold-text)}
.policies{width:396px}
.policy-photo{height:196px;border:4px solid #e8e8e8;background:linear-gradient(90deg,#d9ceb8,#b8a890 50%,#6c6e74)}
.policy-list{list-style:none;display:grid;grid-template-columns:154px 1fr;gap:10px 0;margin-top:16px;font-size:12px}
.policy-list li{display:flex;align-items:center;gap:9px}
.more{display:block;margin-top:16px;font-size:12px;font-weight:700;color:var(--blue)}
.testimonials{width:482px}
.quote{background:#f3f3f3;padding:26px 24px 26px 72px;position:relative;font-style:italic;font-size:12px;line-height:24px;color:#666}
.quote svg{position:absolute;left:22px;top:26px}
.quote:after{content:"";position:absolute;left:40px;bottom:-16px;border:16px solid transparent;border-top-color:#f3f3f3;border-bottom:0}
.author{display:flex;align-items:center;gap:20px;margin-top:24px;padding-left:22px;position:relative}
.avatar{width:70px;height:70px;border-radius:50%;background:#c8ccd0;border:4px solid #e8e8e8}
.author b{display:block;font-size:12px;color:var(--navy)}
.author i{font-size:11px;color:var(--muted)}
.pager{position:absolute;right:0;top:34px;display:flex;gap:4px}
.pager span{width:10px;height:10px;border-radius:50%;background:#bbb}

/* footer */
.footer{height:247px;background:var(--footer);color:#ddd}
.footer .wrap{display:flex;padding-top:40px}
.footer h4{font-size:16px;font-weight:800;color:var(--white);margin-bottom:18px;letter-spacing:.3px}
.links{width:194px}
.links ul{list-style:none;font-size:12px;line-height:25px}
.links li:before{content:"›";margin-right:12px;color:#aaa}
.news{width:312px}
.field{width:240px;height:40px;background:var(--white);border-radius:2px;margin-bottom:12px;display:flex;align-items:center;gap:10px;padding-left:14px;font-size:10px;color:#777}
.submit{display:inline-block;background:var(--gold);color:var(--white);font-size:11px;font-weight:700;padding:10px 36px;border-radius:2px}
.address{width:326px;font-size:12px;line-height:20px}
.address div{display:flex;gap:14px;margin-bottom:16px}
.dates ul{list-style:none;font-size:12px;line-height:25px}
.dates li:before{content:"›";margin-right:12px;color:#aaa}
.pay{display:flex;gap:10px;margin-top:14px}
.pay span{width:32px;height:32px;border-radius:4px;background:#e9e9e9}
.copy{height:48px;background:var(--blue)}
.copy .wrap{height:48px;display:flex;align-items:center;justify-content:space-between;color:var(--white);font-size:11px;font-weight:600}
.social{display:flex;gap:6px;align-items:center}
.social span{width:20px;height:20px;border-radius:50%;border:1px solid var(--white)}
</style>
</head>
<body>
<div class="topline"></div>
<header class="masthead">
  <div class="wrap">
    <div class="brand"><span class="brand-dot"></span><span class="brand-name">Birchford Paw Haven</span></div>
    <div class="head-right">
      <div class="phone">
        <svg width="28" height="28" viewBox="0 0 28 28"><circle cx="14" cy="14" r="12.5" fill="none" stroke="#1a7eae" stroke-width="2"/><path d="M10 8c1 0 2 2 2 3s-1 1-1 2 2 4 4 4 1-1 2-1 3 1 3 2-1 2-2 2c-4 0-10-6-10-10 0-1 1-2 2-2z" fill="#1a7eae"/></svg>
        555-014-2270
      </div>
      <div class="lang"><i></i>English ▾</div>
    </div>
  </div>
</header>
<nav class="mainnav">
  <ul class="wrap">
    <li><a href="#">PHOTO GALLERY</a></li><li><a href="#">ABOUT</a></li><li><a href="#">SERVICES</a></li><li><a href="#">POLICIES</a></li><li><a href="#">MONTHLY NEWSLETTER</a></li><li><a href="#">UNAVAILABLE DATES</a></li><li><a href="#">PAYMENT METHODS</a></li>
  </ul>
</nav>

<section class="hero" role="img" aria-label="Photo of a smiling girl cuddling a dog">
  <div class="hero-shade"></div>
  <svg class="arrow" style="left:34px" width="20" height="50" viewBox="0 0 20 50"><path d="M18 2 2 25l16 23" fill="none" stroke="rgba(255,255,255,.5)" stroke-width="2"/></svg>
  <svg class="arrow" style="right:34px" width="20" height="50" viewBox="0 0 20 50"><path d="M2 2l16 23L2 48" fill="none" stroke="rgba(255,255,255,.5)" stroke-width="2"/></svg>
  <div class="wrap">
    <svg width="76" height="70" viewBox="0 0 76 70"><circle cx="38" cy="35" r="30" fill="none" stroke="#fff" stroke-width="3"/></svg>
    <h1>BIRCHFORD PAW HAVEN</h1>
    <p>Instead of feeling guilty when you must leave your pet for long work days, travel or appointments you can feel good knowing that you have provided your pet with a best friend. Birchford Paw Haven.</p>
    <span class="btn-gold">READ MORE</span>
  </div>
</section>

<section class="welcome">
  <div class="wrap">
    <div class="video" role="img" aria-label="Video still of a girl playing with a small dog on a kitchen floor">
      <svg class="play" width="46" height="34" viewBox="0 0 46 34"><rect width="46" height="34" rx="8" fill="#e02626"/><path d="M18 10v14l12-7z" fill="#fff"/></svg>
    </div>
    <div>
      <h2>WELCOME TO <span>BIRCHFORD PAW HAVEN</span></h2>
      <p>Instead of feeling guilty when you must leave your pet for long work days, travel or appointments you can feel good knowing that you have provided your pet with a best friend. Birchford Paw Haven provides your pet with one on one attention, plenty of play time and exercise and lots and lots of love until your return. I know pets do better and have less stress when they remain in their own homes where the sites, sounds and smells are familiar. They feel safe and comfortable. While you are away there is no need to expose your pet to other pets and possible illness associated with kennels. My pet sitting visits eliminate separation</p>
      <span class="btn-gold">GET MORE INFO</span>
    </div>
  </div>
</section>

<section class="services">
  <div class="wrap">
    <h2 class="section-title">OUR SERVICES</h2>
    <p class="intro">Birchford Paw Haven requests the name and phone number of a person living nearby. We also require contact information for your Veterinarian. Your Veterinarian must be within the neighborhood area.</p>
    <div class="service-row">
      <div class="service">
        <div class="ring"><span><svg width="44" height="44" viewBox="0 0 44 44"><path d="M18 6v20l-5-4-3 3 10 12h14l3-12-12-4V6a3 3 0 0 0-7 0z" fill="#d9a52f"/></svg></span></div>
        <h3>DAILY VISIT - $25.00(PER VISIT)</h3>
        <p>No additional charge for each pet Dog walks or play time for your pet $15.00/ 20</p>
      </div>
      <div class="service">
        <div class="ring"><span><svg width="44" height="44" viewBox="0 0 44 44" fill="none" stroke="#d9a52f" stroke-width="3"><circle cx="22" cy="22" r="13"/><circle cx="22" cy="22" r="4" fill="#d9a52f"/><path d="M22 2v10M22 32v10M2 22h10M32 22h10"/></svg></span></div>
        <h3>POTTY VISITS - $10.00</h3>
        <p>Usually done at noon and bedtime Medication letting them out to potty some</p>
      </div>
      <div class="service">
        <div class="ring"><span><svg width="48" height="44" viewBox="0 0 48 44"><path d="M2 40 18 22l10 8 6-6 12 16z" fill="#d9a52f"/><circle cx="34" cy="10" r="5" fill="#d9a52f"/></svg></span></div>
        <h3>DOG PARK 30 MIN OF PLAY $40</h3>
        <p>Meeting individual pet needs Turning lights on and off Grooming, vet drop off/pic</p>
      </div>
    </div>
  </div>
</section>

<section class="gallery">
  <div class="wrap">
    <h2 class="section-title">OUR GALLERY</h2>
    <p class="intro">Birchford Paw Haven requests the name and phone number of a person living nearby. We also require contact information for your Veterinarian. Your Veterinarian must be within the neighborhood area.</p>
    <div class="thumbs">
      <div class="thumb" role="img" aria-label="Photo of a child with a pet indoors" style="background:linear-gradient(135deg,#5b6a6e,#9aa3a0)"></div>
      <div class="thumb" role="img" aria-label="Photo of a girl playing with a dog on a lawn" style="background:linear-gradient(#6f8a5a,#4f7a3a)"></div>
      <div class="thumb" role="img" aria-label="Photo of a girl greeting a white dog in a garden" style="background:linear-gradient(#6e7a4e,#8a7a5a)"></div>
      <div class="thumb" role="img" aria-label="Photo of a girl holding a grey cat" style="background:linear-gradient(135deg,#b79a84,#8a8e94)"></div>
      <div class="thumb" role="img" aria-label="Photo of a girl sitting on a wooden floor with a dog" style="background:linear-gradient(135deg,#8a5a3a,#b88660)"></div>
      <div class="thumb" role="img" aria-label="Photo of a girl hugging a pet on a chair" style="background:linear-gradient(135deg,#6a4e40,#a89a8a)"></div>
      <div class="thumb" role="img" aria-label="Photo of a girl resting with a fluffy dog" style="background:linear-gradient(135deg,#9aa0a8,#c8b89a)"></div>
      <div class="thumb" role="img" aria-label="Photo of a girl walking a dog in a wooded yard" style="background:linear-gradient(#5a7a4a,#3e5a34)"></div>
    </div>
  </div>
</section>

<section class="info">
  <div class="wrap">
    <div class="policies">
      <h2>OUR <span>POLICIES</span></h2>
      <div class="policy-photo" role="img" aria-label="Photo of a girl in a cap beside a yellow dog"></div>
      <ul class="policy-list">
        <li><svg width="14" height="14" viewBox="0 0 14 14"><circle cx="7" cy="7" r="7" fill="#1a7eae"/><path d="M4 7l2 2 4-4" fill="none" stroke="#fff" stroke-width="1.6"/></svg>Consultation visit</li>
        <li><svg width="14" height="14" viewBox="0 0 14 14"><circle cx="7" cy="7" r="7" fill="#1a7eae"/><path d="M4 7l2 2 4-4" fill="none" stroke="#fff" stroke-width="1.6"/></svg>Dog Park</li>
        <li><svg width="14" height="14" viewBox="0 0 14 14"><circle cx="7" cy="7" r="7" fill="#1a7eae"/><path d="M4 7l2 2 4-4" fill="none" stroke="#fff" stroke-width="1.6"/></svg>Vaccinations</li>
        <li><svg width="14" height="14" viewBox="0 0 14 14"><circle cx="7" cy="7" r="7" fill="#1a7eae"/><path d="M4 7l2 2 4-4" fill="none" stroke="#fff" stroke-width="1.6"/></svg>Cancellations and Early Returns</li>
      </ul>
      <a class="more" href="#">LEARN MORE &gt;&gt;</a>
    </div>
    <div class="testimonials">
      <h2>OUR <span>TESTIMONIALS</span></h2>
      <div class="quote">
        <svg width="36" height="30" viewBox="0 0 36 30"><path d="M0 14C0 6 4 1 12 0v5c-4 1-6 4-6 8h6v17H0zM20 14c0-8 4-13 12-14v5c-4 1-6 4-6 8h6v17H20z" fill="#d2d2d2"/></svg>
        Perspiciatis unde omnis iste natus error sit voluptatem accusantium doloremque laudantium, totam rem aperiam, eaque ipsa quae ab illo inventore veritatis et quasi architecto
      </div>
      <div class="author">
        <div class="avatar" role="img" aria-label="Portrait of the reviewer"></div>
        <div><b>- MARTA LINDQVIST</b><i>Satisfied customers</i></div>
        <div class="pager"><span></span><span></span></div>
      </div>
    </div>
  </div>
</section>

<footer class="footer">
  <div class="wrap">
    <div class="links">
      <h4>QUICK LINKS</h4>
      <ul><li>Photo gallery</li><li>About</li><li>Services</li><li>Policies</li><li>Monthly newsletter</li><li>Unavailable dates</li></ul>
    </div>
    <div class="news">
      <h4>NEWS LETTER</h4>
      <div class="field"><svg width="10" height="10" viewBox="0 0 10 10"><circle cx="5" cy="3" r="2.5" fill="#777"/><path d="M0 10c0-3 2-4 5-4s5 1 5 4z" fill="#777"/></svg>FIRST NAME</div>
      <div class="field"><svg width="12" height="9" viewBox="0 0 12 9"><rect width="12" height="9" fill="#777"/><path d="M0 0l6 5 6-5" fill="none" stroke="#fff"/></svg>EMAIL ADDRESS</div>
      <span class="submit">SUBMIT</span>
    </div>
    <div class="address">
      <h4>ADDRESS</h4>
      <div><svg width="12" height="16" viewBox="0 0 12 16"><path d="M6 0a6 6 0 0 1 6 6c0 4-6 10-6 10S0 10 0 6a6 6 0 0 1 6-6z" fill="#fff"/><circle cx="6" cy="6" r="2" fill="#2b2b2b"/></svg><span>123 Street name,city name,country name,zip code 4579113</span></div>
      <div style="font-size:14px;color:#fff"><svg width="14" height="14" viewBox="0 0 14 14"><path d="M3 0c1 0 2 3 2 4s-1 1-1 2 3 4 4 4 1-1 2-1 4 1 4 2-1 3-3 3C6 14 0 8 0 3 0 1 2 0 3 0z" fill="#fff"/></svg>555-014-2270</div>
      <div><svg width="14" height="11" viewBox="0 0 14 11"><rect width="14" height="11" fill="#fff"/><path d="M0 0l7 6 7-6" fill="none" stroke="#2b2b2b"/></svg>contact@birchfordpawhaven.com</div>
    </div>
    <div class="dates">
      <h4>UNAVAILABLE DATES</h4>
      <ul><li>May 6-8th</li><li>MAY 21-23</li><li>July 3-16</li></ul>
      <div class="pay"><span></span><span></span><span></span><span></span></div>
    </div>
  </div>
</footer>
<div class="copy">
  <div class="wrap">
    <span>COPYRIGHTS©2016BIRCHFORDPAWHAVEN. ALL RIGHTS RESERVED.</span>
    <div class="social"><span></span><span></span><span></span><span></span><span></span><b style="margin-left:10px;font-weight:600">C22</b></div>
  </div>
</div>
</body>
</html>
```